NZ First of it's kind solutions directory and marketplace for busy Mums needs a business card design

We need a business card design for our new nationwide business in NZ (long term plans to go global). We provide solutions to the everyday challenges that busy Mums face by connecting them with quality communities and suppliers of carefully selected, relevant products and services. We sell direct via our online marketplace. The final design should communicate our values of inclusivity, quality and smart solutions. Colours should incorporate our logo colour palette of #477077 and #6ba8b2. Our website is at https://www.brightnestmums.example

Target Market(s)

busy Mums, Age 28 – 50, female, income over $100K, location main centres NZ primarily but NZ wide. Is likely juggling work or career with a young family. Probably had hobbies which have fallen by the wayside.
-Wants to succeed in her chosen career without compromising on family life
-to successfully juggle her career without feeling like she is compromising her children
- Is time poor, something always has to give and it’s generally her health (she’ll stay up late, get stressed)
- probably ex corporate or professional career. Has discretional income

Industry/Entity Type

Business

Contact Information for Business Card

Lena Forbisher, Founder, BrightNestMums.example (Strapline Tap; Gather; Sorted), 47 Kowhai Terrace, Ellerslie, Auckland 1051, New Zealand. Mob: 021 483 517 Ph: +64 (0)9 571 4860

Font styles to use
Other font styles liked:
• Raleway, and/or Architects Daughter

Colors
00a990
33b8a4
86cfc6
cfeae6

Requirements
Must have
• the above details, streamline. the logo and colours associated with those logos
Should not have
• foil or metallic colours

```html
<!DOCTYPE html>
<html lang="en">
<head>
<meta charset="utf-8">
<title>BrightNestMums – Business Card</title>
<link rel="stylesheet" href="https://fonts.googleapis.com/css2?family=Rubik:wght@400;500;700&display=swap">
<style>
  :root {
    --teal-dark: #477077;
    --teal-light: #6ba8b2;
    --ink: #3f666c;
    --paper: #ffffff;
    --backdrop: #e9ebea;
    --photo-warm: #b98a5c;
    --photo-deep: #4d4a4c;
    --photo-soft: #cfc6bb;
  }
  * { box-sizing: border-box; margin: 0; padding: 0; }
  html, body { width: 1200px; height: 930px; overflow: hidden; }
  body {
    background: var(--backdrop);
    font-family: "Rubik", Arial, sans-serif;
    position: relative;
  }
  .card {
    position: absolute;
    width: 620px;
    height: 354px;
    border-radius: 18px;
    overflow: hidden;
    box-shadow: 0 10px 28px rgba(0,0,0,0.18);
  }
  /* Front */
  .card-front { left: 110px; top: 70px; }
  .card-front .photo {
    position: absolute; inset: 0;
    background:
      radial-gradient(ellipse at 40% 30%, rgba(212,150,90,0.85) 0%, rgba(160,110,70,0.5) 35%, transparent 65%),
      linear-gradient(120deg, var(--photo-deep) 0%, var(--photo-warm) 45%, var(--photo-soft) 75%, #8f8a87 100%);
  }
  .card-front .photo::after {
    content: ""; position: absolute; inset: 0;
    background: linear-gradient(180deg, rgba(40,40,45,0.15) 0%, rgba(40,40,45,0.45) 100%);
  }
  .front-brand {
    position: absolute; left: 150px; top: 150px;
    display: flex; align-items: center; gap: 14px;
  }
  .front-brand .mark {
    width: 44px; height: 44px; border-radius: 50%;
    background: var(--paper);
  }
  .front-brand .name {
    color: var(--paper); font-weight: 700; font-size: 40px; letter-spacing: -0.5px;
  }
  .front-url {
    position: absolute; left: 0; right: 0; bottom: 34px;
    text-align: center; color: var(--paper); font-size: 15px; letter-spacing: 0.5px;
  }
  /* Back */
  .card-back { left: 470px; top: 500px; background: var(--paper); }
  .back-mark {
    position: absolute; left: 112px; top: 100px;
    width: 96px; height: 96px; border-radius: 50%;
    background: var(--teal-dark);
  }
  .divider {
    position: absolute; left: 268px; top: 62px;
    width: 2px; height: 150px; background: var(--teal-dark);
  }
  .contact {
    position: absolute; left: 296px; top: 50px;
    color: var(--ink);
  }
  .contact .person { font-size: 30px; font-weight: 700; color: var(--teal-dark); line-height: 1.05; }
  .contact .role { font-size: 16px; margin-bottom: 12px; }
  .contact .address { font-size: 15px; line-height: 1.3; margin-bottom: 6px; }
  .contact .line { display: flex; align-items: center; gap: 7px; font-size: 15px; line-height: 1.35; }
  .contact .line svg { width: 11px; height: 11px; flex: none; }
  .wave { position: absolute; left: 0; bottom: 0; width: 620px; height: 200px; }
</style>
</head>
<body>

<section class="card card-front" aria-label="Card front">
  <div class="photo" role="img" aria-label="Photograph of a tired mother resting her face in her hands, warm soft light"></div>
  <div class="front-brand">
    <span class="mark"></span>
    <span class="name">BrightNestMums</span>
  </div>
  <p class="front-url">www.brightnestmums.example</p>
</section>

<section class="card card-back" aria-label="Card back">
  <span class="back-mark"></span>
  <span class="divider"></span>
  <div class="contact">
    <p class="person">Lena Forbisher</p>
    <p class="role">Founder</p>
    <p class="address">47 Kowhai Terrace, Ellerslie<br>Auckland 1051, New Zealand</p>
    <p class="line">
      <svg viewBox="0 0 12 12"><rect x="3" y="0.5" width="6" height="11" rx="1" fill="none" stroke="currentColor" stroke-width="1.2"/></svg>
      021 483 517
    </p>
    <p class="line">
      <svg viewBox="0 0 12 12"><path d="M2 1 L4.5 1 L5.5 4 L4 5 C5 7 5.5 7.5 7 8.5 L8 7 L11 8 L11 10.5 C6 11.5 0.5 6 2 1 Z" fill="currentColor"/></svg>
      +64 (0)9 571 4860
    </p>
    <p class="line">
      <svg viewBox="0 0 12 12"><circle cx="6" cy="6" r="5" fill="none" stroke="currentColor" stroke-width="1.1"/><ellipse cx="6" cy="6" rx="2.2" ry="5" fill="none" stroke="currentColor" stroke-width="1"/><line x1="1" y1="6" x2="11" y2="6" stroke="currentColor" stroke-width="1"/></svg>
      www.brightnestmums.example
    </p>
  </div>
  <svg class="wave" viewBox="0 0 620 200" preserveAspectRatio="none" aria-hidden="true">
    <path d="M0 178 C200 192 320 168 430 128 C500 102 560 86 620 82 L620 200 L0 200 Z" fill="var(--teal-light)"/>
    <path d="M0 186 C202 198 324 176 434 136 C504 110 564 94 620 90" fill="none" stroke="var(--paper)" stroke-width="3"/>
    <path d="M0 191 C205 202 328 182 438 142 C508 116 566 100 620 96 L620 200 L0 200 Z" fill="var(--teal-dark)"/>
  </svg>
</section>

</body>
</html>
```